Business Card - connecting 2 souls and beggining the journey of self discovery

Logo on the front
with tag line

On the back list of services and contact details

Seminars
workshops
Coaching
podcasts

Darren Whitlow
Health & Wellbeing Life Coach
0491 372 615
darren@brightcoreliving.example
brightcoreliving.example

Industry/Entity Type

Life Coaching

Contact Information for Business Card

I like the use of colour from the logo to be used. I'm not a fan of white.

Requirements
Must have
• My tagline: Your path to balance begins within
Nice to have
• Use of colour that is in the Brightcore Living logo

```html
<!DOCTYPE html>
<html lang="en">
<head>
<meta charset="utf-8">
<title>Brightcore Living – Business Card</title>
<link href="https://fonts.googleapis.com/css2?family=Montserrat:wght@400;600&family=Roboto+Condensed:wght@400;700&display=swap" rel="stylesheet">
<style>
  :root {
    --canvas-bg: #2a2a2a;
    --card-white: #f7f7f7;
    --ink-grey: #6b6b6b;
    --ink-dark: #3a3a3a;
    --coral: #f06a78;
    --orange: #f6a23a;
    --lime: #8fcc5a;
    --green: #5cbf84;
    --teal: #4cb596;
    --purple: #8a3fd6;
    --dot-teal: #3fb8a8;
    --white: #ffffff;
  }
  * { box-sizing: border-box; margin: 0; padding: 0; }
  html, body {
    width: 1200px; height: 886px; overflow: hidden;
    background: var(--canvas-bg);
  }
  .canvas {
    width: 1200px; height: 886px;
    display: flex; flex-direction: column; align-items: center; justify-content: center;
    gap: 50px;
  }
  .card {
    width: 620px; height: 354px; border-radius: 18px;
    position: relative; overflow: hidden;
    box-shadow: 0 10px 30px rgba(0,0,0,.45);
  }

  /* Front */
  .card-front { background: var(--card-white); }
  .front-brand {
    position: absolute; left: 150px; top: 120px;
    display: flex; align-items: center; gap: 22px;
  }
  .brand-dot {
    width: 76px; height: 76px; border-radius: 50%;
    background: linear-gradient(135deg, var(--coral), var(--orange) 45%, var(--lime) 70%, var(--teal));
  }
  .brand-text { font-family: "Montserrat", sans-serif; color: var(--ink-grey); }
  .brand-name { font-size: 30px; font-weight: 400; letter-spacing: -0.5px; line-height: 1.1; }
  .brand-line { font-size: 17px; font-weight: 400; margin-top: 6px; letter-spacing: -0.2px; }
  .front-services {
    position: absolute; right: 48px; bottom: 40px;
    font-family: "Roboto Condensed", sans-serif; font-size: 14px; color: var(--ink-dark);
    line-height: 1.3; text-align: left;
  }
  .front-services .sep { color: var(--dot-teal); margin: 0 4px; }

  /* Back */
  .card-back { background: var(--white); }
  .back-field {
    position: absolute; left: 38px; right: 38px; top: 0; bottom: 0;
    background:
      radial-gradient(ellipse at 25% 35%, rgba(246,162,58,.85), rgba(246,162,58,0) 55%),
      linear-gradient(120deg, var(--coral) 0%, var(--orange) 28%, var(--lime) 52%, var(--green) 72%, var(--teal) 100%);
  }
  .back-badge {
    position: absolute; left: 40px; top: 22px;
    width: 240px; height: 240px; border-radius: 50%;
    border: 3px solid var(--white);
    background: linear-gradient(150deg, var(--orange), var(--lime) 55%, var(--purple) 100%);
    display: flex; align-items: center; justify-content: center; text-align: center;
    font-family: "Montserrat", sans-serif; font-weight: 600; color: var(--white);
    font-size: 30px; line-height: 1.15; letter-spacing: 1px;
  }
  .back-contact {
    position: absolute; left: 300px; top: 170px;
    font-family: "Roboto Condensed", sans-serif; color: var(--white);
  }
  .contact-name { font-size: 22px; font-weight: 700; text-transform: uppercase; letter-spacing: .3px; }
  .contact-role { font-size: 13px; text-transform: uppercase; letter-spacing: .3px; margin-bottom: 10px; }
  .contact-row { display: flex; align-items: center; gap: 7px; font-size: 15px; line-height: 1.4; }
  .contact-row svg { width: 12px; height: 12px; flex: none; }
  .contact-tagline { font-size: 16px; font-weight: 700; margin-top: 14px; }
</style>
</head>
<body>
<main class="canvas">

  <section class="card card-front" aria-label="Card front">
    <div class="front-brand">
      <span class="brand-dot"></span>
      <div class="brand-text">
        <div class="brand-name">Brightcore Living</div>
        <div class="brand-line">Centre for Whole Wellness</div>
      </div>
    </div>
    <div class="front-services">
      <div>Seminars<span class="sep">•</span>Workshops</div>
      <div>Coaching<span class="sep">•</span>Podcasts</div>
    </div>
  </section>

  <section class="card card-back" aria-label="Card back">
    <div class="back-field">
      <div class="back-badge">Brightcore<br>Living</div>
      <div class="back-contact">
        <div class="contact-name">Darren Whitlow</div>
        <div class="contact-role">Health &amp; Wellbeing Life Coach</div>
        <div class="contact-row">
          <svg viewBox="0 0 24 24" aria-hidden="true"><path fill="#fff" d="M6.6 10.8a15.1 15.1 0 0 0 6.6 6.6l2.2-2.2a1 1 0 0 1 1-.25 11.4 11.4 0 0 0 3.6.57 1 1 0 0 1 1 1V20a1 1 0 0 1-1 1A17 17 0 0 1 3 4a1 1 0 0 1 1-1h3.5a1 1 0 0 1 1 1c0 1.25.2 2.45.57 3.57a1 1 0 0 1-.25 1z"/></svg>
          <span>0491 372 615</span>
        </div>
        <div class="contact-row">
          <svg viewBox="0 0 24 24" aria-hidden="true"><path fill="#fff" d="M2 5h20v14H2z"/><path fill="none" stroke="#5cbf84" stroke-width="2" d="M2 5l10 8 10-8"/></svg>
          <span>darren@brightcoreliving.example</span>
        </div>
        <div class="contact-row">
          <svg viewBox="0 0 24 24" aria-hidden="true"><circle cx="12" cy="12" r="10" fill="none" stroke="#fff" stroke-width="2.5"/><path fill="none" stroke="#fff" stroke-width="2" d="M2 12h20M12 2c3 3 3 17 0 20M12 2c-3 3-3 17 0 20"/></svg>
          <span>www.brightcoreliving.example</span>
        </div>
        <div class="contact-tagline">Your path to balance begins within</div>
      </div>
    </div>
  </section>

</main>
</body>
</html>
```